Business Card Design for Occupational Medicine Start Up Company

We need to design a professional business card. We are a healthcare company providing occupational medicine services to blue collar industries. We are professional, efficient and high quality service providers.

Target Market(s)

Blue Collar Industry: Shipbuilding, Ports, Trucking Companies; The Executives and Safety Officers for these companies

Industry/Entity Type

Healthcare

Contact Information for Business Card

Logo, Name, Title, Email, Phone

Other font styles liked:
• Please match our Brand Guide

Requirements
Must have
• Our Company Colors and Logo

```html
<!DOCTYPE html>
<html lang="en">
<head>
<meta charset="utf-8">
<title>Harborline Business Card</title>
<link href="https://fonts.googleapis.com/css2?family=Lato:wght@400;700&family=Ubuntu:wght@400;500&display=swap" rel="stylesheet">
<style>
  :root {
    --backdrop: #adafae;
    --paper: #ffffff;
    --navy: #2b3a8c;
    --sky: #16a3dc;
    --ink: #4a4a4a;
    --back-blue: #2e3a8e;
    --back-blue-light: #34449a;
    --white: #ffffff;
  }
  * { margin: 0; padding: 0; box-sizing: border-box; }
  html, body { width: 1200px; height: 1200px; overflow: hidden; }
  body { background: var(--backdrop); position: relative; font-family: "Lato", sans-serif; }

  .card { position: absolute; left: 222px; width: 756px; height: 463px; }
  .card--front { top: 109px; background: var(--paper); }
  .card--back {
    top: 630px;
    background: linear-gradient(160deg, var(--back-blue-light), var(--back-blue) 60%);
  }

  .brand { position: absolute; text-align: center; }
  .brand__dot { display: block; margin: 0 auto; border-radius: 50%; }
  .brand__name { font-family: "Lato", sans-serif; font-weight: 700; letter-spacing: 1px; }

  .card--front .brand { left: 56px; width: 320px; top: 160px; }
  .card--front .brand__dot { width: 78px; height: 78px; background: var(--sky); margin-bottom: 22px; }
  .card--front .brand__name { color: var(--navy); font-size: 38px; }

  .card--back .brand { left: 0; width: 100%; top: 118px; }
  .card--back .brand__dot { width: 128px; height: 128px; background: var(--white); margin-bottom: 42px; }
  .card--back .brand__name { color: var(--white); font-size: 58px; letter-spacing: 3px; }

  .name-band {
    position: absolute; left: 416px; top: 106px; width: 340px; height: 74px;
    background: var(--sky); border-left: 14px solid var(--navy);
    padding: 2px 0 0 17px; font-family: "Ubuntu", sans-serif;
  }
  .name-band__name { color: var(--navy); font-size: 38px; font-weight: 500; line-height: 44px; }
  .name-band__title { color: var(--white); font-size: 22px; line-height: 26px; }

  .contact { position: absolute; left: 416px; top: 236px; list-style: none; }
  .contact__item { display: flex; align-items: center; height: 31.5px; color: var(--ink); font-size: 21px; }
  .contact__icon { width: 20px; height: 20px; margin-right: 11px; fill: var(--sky); }
</style>
</head>
<body>
  <section class="card card--front">
    <div class="brand">
      <span class="brand__dot"></span>
      <span class="brand__name">HARBORLINE</span>
    </div>
    <div class="name-band">
      <div class="name-band__name">Dana Ruell</div>
      <div class="name-band__title">Account Executive</div>
    </div>
    <ul class="contact">
      <li class="contact__item">
        <svg class="contact__icon" viewBox="0 0 20 20"><path d="M4 1l4 4-2 3c1 2 4 5 6 6l3-2 4 4-3 3C9 19 1 11 1 4z"/></svg>
        555.210.4836
      </li>
      <li class="contact__item">
        <svg class="contact__icon" viewBox="0 0 20 20"><rect x="5" y="1" width="10" height="5"/><rect x="1" y="7" width="18" height="8" rx="2"/><rect x="5" y="12" width="10" height="7" fill="#fff" stroke="#16a3dc" stroke-width="2"/></svg>
        555.210.4837
      </li>
      <li class="contact__item">
        <svg class="contact__icon" viewBox="0 0 20 20"><path d="M1 3h17v4l-8.5 6L1 7z"/><path d="M1 9l8.5 6 5-3.5V16H1z"/><circle cx="16" cy="15" r="4"/></svg>
        druell@harborline.com
      </li>
      <li class="contact__item">
        <svg class="contact__icon" viewBox="0 0 20 20" fill="none" stroke="#16a3dc" stroke-width="1.5"><circle cx="10" cy="10" r="8.5"/><ellipse cx="10" cy="10" rx="4" ry="8.5"/><path d="M1.5 10h17M3 5.5h14M3 14.5h14"/></svg>
        www.harborline.com
      </li>
    </ul>
  </section>

  <section class="card card--back">
    <div class="brand">
      <span class="brand__dot"></span>
      <span class="brand__name">HARBORLINE</span>
    </div>
  </section>
</body>
</html>
```